Tall Fern Roofing Business Card

Need a business card with the logo that was designed here

Contact Information for Business Card

Name, Title, Phone, Email, Website, Company name

```html
<!DOCTYPE html>
<html lang="en">
<head>
<meta charset="utf-8">
<title>Tall Fern Roofing Business Card</title>
<link rel="stylesheet" href="https://fonts.googleapis.com/css2?family=Poppins:wght@400;700&family=Great+Vibes&display=swap">
<style>
  :root {
    --backdrop: #1c1c1c;
    --brand-blue: #1f75c0;
    --card-white: #ffffff;
    --ink-grey: #8a8b8d;
    --line-grey: #9a9b9d;
  }
  * { margin: 0; padding: 0; box-sizing: border-box; }
  html, body { width: 1200px; height: 1015px; overflow: hidden; }
  body { background: var(--backdrop); font-family: "Poppins", sans-serif; position: relative; }

  .card {
    position: absolute;
    width: 520px;
    height: 297px;
    overflow: hidden;
    box-shadow: 0 12px 30px rgba(0,0,0,.55);
  }
  .card--back { left: 80px; top: 110px; background: var(--brand-blue); }
  .card--front { left: 600px; top: 580px; background: var(--card-white); }

  .wordmark {
    position: absolute;
    z-index: 1;
    display: flex;
    align-items: center;
    gap: 10px;
    font-family: "Poppins", sans-serif;
    font-weight: 700;
    font-size: 30px;
    letter-spacing: .5px;
    white-space: nowrap;
  }
  .wordmark__square { width: 14px; height: 14px; }
  .card--back .wordmark { left: 50%; top: 50%; transform: translate(-50%, -50%); color: var(--card-white); }
  .card--back .wordmark__square { background: var(--card-white); }
  .card--front .wordmark { left: 34px; top: 70px; font-size: 24px; color: var(--brand-blue); }
  .card--front .wordmark__square { background: var(--brand-blue); width: 12px; height: 12px; }

  .wave { position: absolute; inset: 0; width: 100%; height: 100%; }

  .person { position: absolute; z-index: 1; right: 26px; top: 22px; text-align: right; }
  .person__name { line-height: 1; white-space: nowrap; }
  .person__first { font-family: "Great Vibes", cursive; font-size: 34px; color: var(--brand-blue); }
  .person__last { font-weight: 700; font-size: 20px; color: var(--ink-grey); margin-left: 4px; }
  .person__title { font-size: 14px; color: var(--ink-grey); margin-top: 2px; }

  .contact { position: absolute; z-index: 1; right: 22px; top: 178px; list-style: none; }
  .contact__item {
    display: flex; justify-content: flex-end; align-items: center; gap: 8px;
    color: var(--card-white); font-size: 15px; line-height: 23px;
  }
  .contact__icon { width: 15px; height: 15px; flex: none; }
</style>
</head>
<body>

  <section class="card card--back" aria-label="Card back">
    <div class="wordmark"><span class="wordmark__square"></span>Tall Fern Roofing</div>
  </section>

  <section class="card card--front" aria-label="Card front">
    <svg class="wave" viewBox="0 0 520 297" aria-hidden="true">
      <path d="M0,168 C110,190 190,176 250,136 C290,110 320,98 350,92" fill="none" stroke="var(--line-grey)" stroke-width="7"/>
      <path d="M0,180 C120,200 210,186 270,144 C330,104 400,98 490,96" fill="none" stroke="var(--brand-blue)" stroke-width="5"/>
      <path d="M0,192 C130,210 220,196 284,152 C340,116 410,110 520,106 L520,297 L0,297 Z" fill="var(--brand-blue)"/>
    </svg>

    <div class="wordmark"><span class="wordmark__square"></span>Tall Fern Roofing</div>

    <div class="person">
      <div class="person__name"><span class="person__first">Daniel</span><span class="person__last">HARPER</span></div>
      <div class="person__title">Managing Director</div>
    </div>

    <ul class="contact">
      <li class="contact__item">044-555 210 387
        <svg class="contact__icon" viewBox="0 0 16 16" aria-hidden="true"><path d="M3 1.5l3 3-1.6 1.6a9 9 0 0 0 5.5 5.5L11.5 10l3 3-2 2C6.5 15 1 9.5 1 3.5z" fill="var(--card-white)"/></svg>
      </li>
      <li class="contact__item">info@tallfernroofing.com
        <svg class="contact__icon" viewBox="0 0 16 16" aria-hidden="true"><rect x="1" y="3" width="14" height="10" fill="none" stroke="var(--card-white)" stroke-width="1.6"/><path d="M1 3l7 6 7-6" fill="none" stroke="var(--card-white)" stroke-width="1.6"/></svg>
      </li>
      <li class="contact__item">www.tallfernroofing.com
        <svg class="contact__icon" viewBox="0 0 16 16" aria-hidden="true"><g fill="none" stroke="var(--card-white)" stroke-width="1.4"><circle cx="8" cy="8" r="6.5"/><ellipse cx="8" cy="8" rx="3" ry="6.5"/><path d="M1.5 8h13M2.5 4.5h11M2.5 11.5h11"/></g></svg>
      </li>
    </ul>
  </section>

</body>
</html>
```